Merry Perch Wild Bird Food Gusset Bag Deisgn

We’re looking to transition from our current packaging—using a sticker on a bag—to a fully printed film design. The goal is to modernize the look and make it more fun while staying true to our existing brand identity.
We’d like to retain the same color scheme, fonts, and artwork style currently used on our bags. The barcode and product information should be placed on the back of the bag.
Bag specifications:
Dimensions: 410mm (length) x 530mm (width)
Design: Predominantly white with strategically placed transparent areas to allow the product to be seen inside.
There are 10 different bag designs required for this range.
We have attached our current labels of each product there is a Circle one and also a rectangle one that all all product information
We would also likes explained and also a image showing the these 5L bags refill 5L Tubs
We’ll also attach some example bags that represent the look and feel we’re aiming for in the new designs.
The bag is a gusset bag, Icon attached as an example
Target Market(s)
Wild Bird Food Buyers
Look and feel

```html
<!DOCTYPE html>
<html lang="en">
<head>
<meta charset="utf-8">
<title>Merry Perch – Black Sunflower 5lbs Bag</title>
<link href="https://fonts.googleapis.com/css2?family=Baloo+2:wght@700&family=Chewy&family=Oswald:wght@400;600&display=swap" rel="stylesheet">
<style>
  :root {
    --teal: #0f8a7c;
    --teal-dark: #0b6f64;
    --white: #f7f7f5;
    --ink: #151515;
    --backdrop: #b9b9b9;
    --seed-dark: #2c2c2e;
    --seed-mid: #5a5b5e;
    --leaf: #3f8f3a;
    --petal: #f2b01e;
    --stone: #7f8fa6;
  }
  * { box-sizing: border-box; margin: 0; padding: 0; }
  html, body { width: 1142px; height: 1200px; overflow: hidden; }
  body {
    background: var(--backdrop);
    position: relative;
    font-family: "Oswald", sans-serif;
  }
  .gusset {
    position: absolute; left: 90px; top: 110px; width: 220px; height: 980px;
    background: var(--teal-dark);
    color: var(--white);
    padding: 330px 22px 0;
    font-size: 11.5px; line-height: 1.6;
  }
  .gusset h3 { font-weight: 600; font-size: 13px; text-align: center; text-transform: uppercase; line-height: 1.4; margin-bottom: 8px; }
  .gusset p { margin-bottom: 10px; }
  .gusset .label { font-weight: 600; margin-bottom: 2px; }
  .front {
    position: absolute; left: 310px; top: 110px; width: 740px; height: 980px;
    background: var(--teal);
  }
  .front-band {
    position: absolute; left: 80px; top: 0; width: 580px; height: 980px;
    background: var(--white);
  }
  .brand {
    position: absolute; top: 120px; left: 0; width: 100%;
    display: flex; align-items: center; justify-content: center; gap: 10px;
  }
  .brand-dot { width: 38px; height: 38px; border-radius: 50%; background: var(--teal); }
  .brand-name {
    font-family: "Baloo 2", sans-serif; font-weight: 700; font-size: 32px;
    color: var(--teal); line-height: 1;
  }
  .title {
    position: absolute; top: 210px; left: 0; width: 100%;
    font-family: "Chewy", sans-serif; color: var(--ink);
    text-align: center; line-height: 0.95;
  }
  .title .line1 { display: block; font-size: 112px; }
  .title .line2 { display: block; font-size: 112px; letter-spacing: -1px; }
  .scene {
    position: absolute; left: 0; top: 440px; width: 580px; height: 330px;
  }
  .seed-window {
    position: absolute; left: 0; top: 770px; width: 580px; height: 210px;
    background: linear-gradient(180deg, var(--seed-mid), var(--seed-dark));
  }
  .weight {
    position: absolute; right: 10px; top: 730px;
    font-family: "Baloo 2", sans-serif; font-weight: 700; font-size: 44px;
    color: var(--ink);
  }
</style>
</head>
<body>
  <aside class="gusset">
    <h3>Attract a variety of birds with Merry Perch black sunflower seeds</h3>
    <p>Turn your garden into a haven with our black sunflower seeds, a rich source of oil and energy that draws finches, tits and sparrows all year round.</p>
    <h3>Easy to use</h3>
    <p>Fill your feeder, bird table or scatter on the ground to bring cheerful visitors to your garden every day.</p>
    <p class="label">Address:</p>
    <p>Fernbrook Supplies, Unit 4 Millbank Business Park, Ashdale AB1 2CD</p>
    <p class="label">Contact:</p>
    <p>sales@fernbrooksupplies.co.uk</p>
  </aside>

  <section class="front">
    <div class="front-band">
      <div class="brand">
        <span class="brand-dot"></span>
        <span class="brand-name">merry perch</span>
      </div>
      <h1 class="title"><span class="line1">Black</span><span class="line2">Sunflower</span></h1>
      <svg class="scene" viewBox="0 0 580 330" role="img" aria-label="Illustration of a chickadee perched on stones among sunflowers, grasses and scattered black seeds">
        <defs>
          <linearGradient id="sceneTone" x1="0" y1="0" x2="1" y2="1">
            <stop offset="0" stop-color="#9fc48e"/>
            <stop offset="0.5" stop-color="#5e9a4c"/>
            <stop offset="1" stop-color="#e9b63a"/>
          </linearGradient>
        </defs>
        <rect x="20" y="10" width="540" height="320" rx="40" fill="url(#sceneTone)" opacity="0.85"/>
      </svg>
      <div class="seed-window" role="img" aria-label="Clear window showing black sunflower seeds inside the bag"></div>
      <div class="weight">5lbs</div>
    </div>
  </section>
</body>
</html>
```